Floor Inspections and Consulting

We provide inspections and consulting services on various floor coverings, e.g. carpet, hardwood, etc. We also do expert witness work for attorneys due to floor covering failures. We current have a logo, just need it incorporated into a new design. I have examples of cards I have found on the internet that capture my attention and make a statement. I have included our original business card, which in my opinion is terrible, but it does have our logo on it.

```html
<!DOCTYPE html>
<html lang="en">
<head>
<meta charset="utf-8">
<title>Summit Floor Inspections – Business Card</title>
<link href="https://fonts.googleapis.com/css2?family=Montserrat:wght@500;600;700&display=swap" rel="stylesheet">
<style>
  :root {
    --backdrop: #2b2b2b;
    --wood-light: #e6d2b4;
    --wood-mid: #d9bf9a;
    --wood-warm: #cfae86;
    --ink: #7f6552;
    --ink-soft: #8d7462;
    --rule: #5c4a3d;
  }
  * { box-sizing: border-box; margin: 0; padding: 0; }
  html, body {
    width: 1200px; height: 866px; overflow: hidden;
    background: var(--backdrop);
    font-family: "Montserrat", sans-serif;
  }
  .card-set {
    position: absolute; top: 284px; left: 60px;
    display: flex; gap: 40px;
  }
  .card {
    position: relative; width: 520px; height: 297px;
    overflow: hidden; color: var(--ink);
  }
  .wood-surface {
    position: absolute; inset: 0;
    background: linear-gradient(172deg, var(--wood-light) 0%, var(--wood-mid) 45%, var(--wood-light) 70%, var(--wood-warm) 100%);
  }
  .rule {
    position: absolute; height: 1px; background: var(--rule);
  }
  .content { position: absolute; inset: 0; }

  /* Front: company side */
  .front .rule-top { top: 62px; left: 110px; width: 340px; }
  .front .rule-bottom { top: 206px; left: 70px; width: 400px; }
  .brand-block {
    position: absolute; top: 76px; left: 0; right: 0; text-align: center;
  }
  .brand-mark {
    display: inline-block; width: 18px; height: 18px; border-radius: 50%;
    background: var(--ink); margin-bottom: 8px;
  }
  .brand-name {
    font-weight: 700; font-size: 27px; letter-spacing: 2px;
    line-height: 1.05; text-transform: uppercase; color: var(--ink);
  }
  .brand-sub {
    font-weight: 600; font-size: 10px; letter-spacing: 3px;
    text-transform: uppercase; margin-top: 5px;
  }
  .tagline {
    position: absolute; top: 222px; left: 0; right: 0; text-align: center;
    font-weight: 500; font-size: 13px; letter-spacing: 0.5px; color: var(--ink-soft);
  }

  /* Back: contact side */
  .back .rule-top { top: 42px; left: 80px; width: 360px; }
  .back .rule-mid { top: 150px; left: 60px; width: 420px; }
  .back .rule-bottom { top: 262px; left: 40px; width: 360px; }
  .back .brand-block { top: 60px; }
  .back .brand-name { font-size: 22px; }
  .contact {
    position: absolute; top: 164px; left: 0; right: 0; text-align: center;
  }
  .person-name {
    font-weight: 700; font-size: 20px; letter-spacing: 2px; text-transform: uppercase;
  }
  .contact-line {
    font-weight: 600; font-size: 15px; letter-spacing: 0.5px; margin-top: 4px;
  }
</style>
</head>
<body>
  <main class="card-set">
    <section class="card front">
      <div class="wood-surface" role="img" aria-label="Light natural wood grain texture"></div>
      <div class="content">
        <div class="rule rule-top"></div>
        <div class="brand-block">
          <span class="brand-mark"></span>
          <h1 class="brand-name">Summit Floor<br>Inspections</h1>
          <p class="brand-sub">Analysis &amp; Consulting</p>
        </div>
        <div class="rule rule-bottom"></div>
        <p class="tagline">Certified Floor Covering Inspection &amp; Consulting</p>
      </div>
    </section>

    <section class="card back">
      <div class="wood-surface" role="img" aria-label="Light natural wood grain texture"></div>
      <div class="content">
        <div class="rule rule-top"></div>
        <div class="brand-block">
          <span class="brand-mark"></span>
          <p class="brand-name">Summit Floor Inspections</p>
        </div>
        <div class="rule rule-mid"></div>
        <div class="contact">
          <p class="person-name">Daniel Marsh</p>
          <p class="contact-line">303-555-0142</p>
          <p class="contact-line">daniel@summitfloorpro.com</p>
          <p class="contact-line">www.summitfloorpro.com</p>
        </div>
        <div class="rule rule-bottom"></div>
      </div>
    </section>
  </main>
</body>
</html>
```